Detail Shop Business card design

i need a business card design for my new detailing company called 'Brisk's Polish Works'. i want an all black and white design . simple, direct and to the point. i want the designer to choose a fitting font to match the logothe front should have logo, address, phone and email and the back side should have a slogan and text indicating that we offer services on anything including cars, trucks, motorcycles and RVs. slogan will read "we take pride in your ride"
maybe also very small on the back side the IG icon with Brisks_Polish_Works

phone 208.417.6352
address 3847 E Larkin Ave
Spokane WA 99214
email: BrisksPolish@mailvexo.com

Target Market(s)

all ages , auto enthusiasts

Industry/Entity Type

Automotive

Contact Information for Business Card

the front should have logo, address, phone and email and the back side should have a slogan and text indicating that we offer services on anything including cars, trucks, motorcycles and RVs. slogan will read "we take pride in your ride"

phone 208.417.6352
address 3847 E Larkin Ave
Spokane WA 99214

Colors
000000
ffffff

Requirements
Must have
• bold font and very simple design with good spacing
Nice to have
• anything creative from the designer indicating we service any types of vehicles
Should not have
• any colors ,

```html
<!DOCTYPE html>
<html lang="en">
<head>
<meta charset="utf-8">
<title>Brisk's Polish Works – Business Card</title>
<link href="https://fonts.googleapis.com/css2?family=Lato:wght@400;700&display=swap" rel="stylesheet">
<style>
  :root {
    --ink: #0b0b0b;
    --paper: #f1f1f1;
    --backdrop: #3c3c3c;
    --rule-dark: #9a9a9a;
    --rule-light: #6a6a6a;
  }
  * { margin: 0; padding: 0; box-sizing: border-box; }
  html, body { width: 1200px; height: 896px; overflow: hidden; }
  body {
    background: var(--backdrop);
    font-family: 'Lato', sans-serif;
    display: flex;
    align-items: center;
    justify-content: center;
    gap: 40px;
  }
  .card {
    position: relative;
    width: 540px;
    height: 309px;
    overflow: hidden;
  }
  .card--front { background: var(--paper); color: var(--ink); }
  .card--back { background: var(--ink); color: var(--paper); }
  .band {
    position: absolute;
    left: 0; top: 0;
    width: 100%; height: 84px;
  }
  .card--front .band { background: var(--ink); }
  .card--back .band { background: var(--paper); }
  .badge {
    position: absolute;
    left: 195px; top: 28px;
    width: 150px; height: 150px;
    border-radius: 50%;
    display: flex;
    flex-direction: column;
    align-items: center;
    justify-content: center;
    text-align: center;
  }
  .card--front .badge { background: var(--paper); }
  .card--back .badge { background: var(--ink); }
  .brand-name {
    font-weight: 700;
    font-size: 21px;
    line-height: 1.15;
    text-transform: uppercase;
    letter-spacing: 0.5px;
  }
  .rule {
    position: absolute;
    left: 150px;
    width: 240px;
    height: 1px;
  }
  .card--front .rule { background: var(--rule-light); }
  .card--back .rule { background: var(--rule-dark); }
  .social {
    position: absolute;
    left: 0; top: 192px;
    width: 100%;
    display: flex;
    flex-direction: column;
    align-items: center;
    gap: 3px;
    font-size: 14px;
  }
  .social-dot {
    width: 13px; height: 13px;
    border-radius: 50%;
    background: var(--ink);
  }
  .contact {
    position: absolute;
    top: 248px;
    font-size: 14.5px;
    line-height: 1.35;
  }
  .contact--address { left: 92px; }
  .contact--lines { left: 268px; }
  .contact-line { display: flex; align-items: center; gap: 6px; }
  .contact-line svg { width: 12px; height: 12px; flex: none; }
  .slogan {
    position: absolute;
    left: 0; top: 190px;
    width: 100%;
    text-align: center;
    font-size: 22px;
    font-weight: 700;
    letter-spacing: 0.3px;
  }
  .services {
    position: absolute;
    left: 0; top: 238px;
    width: 100%;
    text-align: center;
    font-size: 14px;
    line-height: 1.4;
  }
</style>
</head>
<body>
  <section class="card card--front" aria-label="Card front">
    <div class="band"></div>
    <div class="badge"><span class="brand-name">Brisk's<br>Polish<br>Works</span></div>
    <div class="rule" style="top:186px"></div>
    <div class="social">
      <span class="social-dot" aria-hidden="true"></span>
      <span class="social-handle">Brisks_Polish_Works</span>
    </div>
    <div class="rule" style="top:236px"></div>
    <div class="contact contact--address">
      <div>3847 E Larkin Ave</div>
      <div>Spokane WA 99214</div>
    </div>
    <div class="contact contact--lines">
      <div class="contact-line">
        <svg viewBox="0 0 12 12" aria-hidden="true"><path d="M1 3.5C1 2 2.5 1.5 6 1.5S11 2 11 3.5L9 4.5 8.5 3.5h-5L3 4.5zM3 5h6l1 5H2z" fill="#0b0b0b"/><circle cx="6" cy="7.4" r="1.3" fill="#f1f1f1"/></svg>
        <span>208.417.6352</span>
      </div>
      <div class="contact-line">
        <svg viewBox="0 0 12 12" aria-hidden="true"><rect x="0.5" y="2.5" width="11" height="7.5" fill="#0b0b0b"/><path d="M1 3l5 4 5-4" stroke="#f1f1f1" stroke-width="1" fill="none"/></svg>
        <span>BrisksPolish@mailvexo.com</span>
      </div>
    </div>
  </section>

  <section class="card card--back" aria-label="Card back">
    <div class="band"></div>
    <div class="badge"><span class="brand-name">Brisk's<br>Polish<br>Works</span></div>
    <h1 class="slogan">WE TAKE PRIDE IN YOUR RIDE</h1>
    <div class="rule" style="top:226px"></div>
    <p class="services">We offer services on including cars, trucks<br>motorcycles and RVs.</p>
  </section>
</body>
</html>
```